Simple Logo Design for Semi-Clear Plastic Frosted Card stock

Create a business card on frosted plastic. compliment existing logo elements with a tree trunk, roots, or seed at the lower half and the full logo both on the front.

Contact information will go on a solid portion of the back of this design since this card stock is semi-transparent.

It is important to consider this plastic card stock medium in your design. I found helpful tips and guides listed at vellaprint-sample.net: be careful to understand ink printed on plastic cards cannot have too much of a consistent print area or risks peeling and fine lines can easily scratch off.
Updates

2" x 3.5" 20PT Clear Plastic Business cards with Round corners Please get info or templates here: https://www.vellaprint-sample.net/product-detail/2-x-35-20pt-clear-plastic-business-cards-with-round-corners

Target Market(s)

Not for profit- religion

Industry/Entity Type

Business

Must include complementary elements to the existing logo

Font styles to use
Decorative

Colors
000000

Requirements
Must have
• Elements of community, nature and oneness. Such as: seed, roots, tree trunk, etc.
• Three lines of space on the back for Name, Title, Phone Number.
Nice to have
• I like a light use of decorative elements
Should not have
• No eyes, from faces or animals.

```html
<!DOCTYPE html>
<html lang="en">
<head>
<meta charset="utf-8">
<title>Kindred Grove – Frosted Business Cards</title>
<link href="https://fonts.googleapis.com/css2?family=Cinzel:wght@400;600&family=Jost:wght@400;500&display=swap" rel="stylesheet">
<style>
  :root {
    --page-bg: #dfe3e6;
    --frost: #eef1f3;
    --frost-edge: #cfd6db;
    --ink-dark: #2c4343;
    --ink-green: #2f6b3a;
    --ink-soft: #556666;
    --rule: #b9c3c7;
  }
  * { margin: 0; padding: 0; box-sizing: border-box; }
  html, body { width: 800px; height: 1200px; overflow: hidden; }
  body {
    background: var(--page-bg);
    display: flex;
    flex-direction: column;
    align-items: center;
    justify-content: center;
    gap: 120px;
  }
  .card {
    position: relative;
    width: 580px;
    height: 331px;
    border-radius: 18px;
    background: linear-gradient(160deg, #f4f6f7 0%, var(--frost) 55%, #e6eaed 100%);
    border: 1px solid var(--frost-edge);
    box-shadow: 0 10px 30px rgba(40, 60, 70, 0.12);
    overflow: hidden;
  }
  .brand {
    position: absolute;
    display: flex;
    flex-direction: column;
    align-items: center;
  }
  .brand-mark {
    display: block;
    border-radius: 50%;
    background: var(--ink-green);
  }
  .brand-name {
    font-family: "Jost", sans-serif;
    font-weight: 500;
    color: var(--ink-dark);
    letter-spacing: 0.02em;
    text-transform: uppercase;
    line-height: 1;
    white-space: nowrap;
  }
  .brand-tagline {
    font-family: "Cinzel", serif;
    font-weight: 400;
    color: var(--ink-dark);
    letter-spacing: 0.04em;
    text-transform: uppercase;
    line-height: 1;
    white-space: nowrap;
  }

  /* Back: contact card */
  .card-back .brand { top: 24px; right: 26px; }
  .card-back .brand-mark { width: 72px; height: 72px; margin-bottom: 10px; }
  .card-back .brand-name { font-size: 27px; }
  .card-back .brand-tagline { font-size: 10.5px; margin-top: 6px; }

  .contact {
    position: absolute;
    left: 0;
    right: 0;
    top: 228px;
  }
  .contact-accent {
    position: absolute;
    left: 0;
    top: 2px;
    width: 5px;
    height: 26px;
    background: var(--ink-dark);
  }
  .contact-name {
    font-family: "Cinzel", serif;
    font-weight: 600;
    font-size: 19px;
    line-height: 22px;
    color: var(--ink-dark);
    padding-left: 22px;
    letter-spacing: 0.03em;
  }
  .contact-title {
    font-family: "Cinzel", serif;
    font-size: 10px;
    line-height: 12px;
    color: var(--ink-soft);
    padding-left: 22px;
    letter-spacing: 0.05em;
  }
  .contact-rule {
    height: 1px;
    background: var(--rule);
    margin-top: 4px;
  }
  .contact-lines {
    list-style: none;
    padding-left: 22px;
    margin-top: 16px;
    font-family: "Cinzel", serif;
    font-size: 10.5px;
    color: var(--ink-soft);
    letter-spacing: 0.04em;
  }
  .contact-lines li { line-height: 16px; }

  /* Front: full mark */
  .card-front .brand { top: 66px; left: 0; right: 0; }
  .card-front .brand-mark { width: 96px; height: 96px; margin-bottom: 20px; }
  .card-front .brand-name { font-size: 44px; }
  .card-front .brand-tagline { font-size: 13px; margin-top: 8px; }
</style>
</head>
<body>

  <section class="card card-back" aria-label="Card back with contact details">
    <div class="brand">
      <span class="brand-mark" aria-hidden="true"></span>
      <span class="brand-name">Kindred Grove</span>
      <span class="brand-tagline">Learning, Fellowship &amp; Harmony</span>
    </div>
    <div class="contact">
      <span class="contact-accent" aria-hidden="true"></span>
      <p class="contact-name">Dana Whitfield</p>
      <p class="contact-title">Director</p>
      <div class="contact-rule"></div>
      <ul class="contact-lines">
        <li>555 0142-7781</li>
        <li>danawhitfieldmail.com</li>
      </ul>
    </div>
  </section>

  <section class="card card-front" aria-label="Card front with brand">
    <div class="brand">
      <span class="brand-mark" aria-hidden="true"></span>
      <span class="brand-name">Kindred Grove</span>
      <span class="brand-tagline">Learning, Fellowship &amp; Harmony</span>
    </div>
  </section>

</body>
</html>
```